Visitenkarten-Design für Forschungs- und Beratungsunternehmen
Zielgruppe
*Fervolia' ist ein Forschungs- und Beratungsunternehmen für Lebensmittelwirkungen. Unsere Angebote sind: Vorträge, Workshops, Seminare und Coaching. Die Zielgruppen sind Pädagogen, Mediziner, Psychologen u.a.m.
Aufgabenstellung
Bei Bedarf kann die Gestaltung der Visitenkarte auch auf die Rückseite ausgedehnt werden.

```html
<!DOCTYPE html>
<html lang="de">
<head>
<meta charset="utf-8">
<title>Fervolia – Visitenkarte</title>
<link rel="stylesheet" href="https://fonts.googleapis.com/css2?family=Montserrat:wght@700&family=Open+Sans:wght@400;600&display=swap">
<style>
  :root {
    --stage: #1b1b1b;
    --card-light: #ffffff;
    --card-dark: #262626;
    --text-dark: #2b2b2b;
    --text-muted: #6a6a6a;
    --text-light: #d8d8d8;
    --ring-yellow: #f2c12e;
    --ring-pink: #d63aa5;
    --ring-purple: #8a3fc2;
  }
  html, body {
    margin: 0;
    width: 1200px;
    height: 901px;
    overflow: hidden;
    background: var(--stage);
  }
  .stage {
    position: relative;
    width: 1200px;
    height: 901px;
    display: flex;
    align-items: center;
    justify-content: center;
    gap: 48px;
  }
  .card {
    position: relative;
    width: 525px;
    height: 300px;
    overflow: hidden;
    box-shadow: 0 18px 40px rgba(0,0,0,.55);
  }
  .card-front { background: var(--card-light); }
  .card-back {
    background: var(--card-dark);
    display: flex;
    align-items: center;
    justify-content: center;
  }
  .front-shape { position: absolute; inset: 0; }
  .identity {
    position: absolute;
    top: 74px;
    left: 0;
    width: 100%;
    text-align: center;
    font-family: "Open Sans", sans-serif;
  }
  .identity-name {
    margin: 0;
    font-family: "Montserrat", sans-serif;
    font-weight: 700;
    font-size: 17px;
    letter-spacing: .5px;
    color: var(--text-dark);
  }
  .identity-role {
    margin: 2px 0 0;
    font-size: 11px;
    color: var(--text-muted);
  }
  .contacts {
    position: absolute;
    left: 0;
    right: 0;
    bottom: 24px;
    display: flex;
    justify-content: space-around;
    font-family: "Open Sans", sans-serif;
    color: var(--text-light);
    font-size: 11.5px;
    line-height: 1.45;
    text-align: center;
  }
  .contact { display: flex; flex-direction: column; align-items: center; gap: 8px; }
  .contact-icon { width: 26px; height: 26px; }
  .brand {
    display: flex;
    align-items: center;
    gap: 14px;
    font-family: "Open Sans", sans-serif;
    font-weight: 600;
    font-size: 40px;
    color: #ffffff;
    letter-spacing: 1px;
  }
  .brand-dot { width: 22px; height: 22px; border-radius: 50%; background: #ffffff; }
</style>
</head>
<body>
<main class="stage">
  <section class="card card-front">
    <svg class="front-shape" viewBox="0 0 525 300" width="525" height="300" aria-hidden="true">
      <defs>
        <linearGradient id="spectrum" x1="0" y1="0" x2="1" y2="0">
          <stop offset="0" stop-color="#1fa3e0"/>
          <stop offset=".25" stop-color="#6cc04a"/>
          <stop offset=".45" stop-color="#f2c12e"/>
          <stop offset=".62" stop-color="#f06a2a"/>
          <stop offset=".8" stop-color="#d63aa5"/>
          <stop offset="1" stop-color="#7b3fc2"/>
        </linearGradient>
      </defs>
      <path d="M0 200 Q160 130 525 120 L525 300 L0 300 Z" fill="var(--card-dark)"/>
      <path d="M0 200 Q160 130 525 120" fill="none" stroke="url(#spectrum)" stroke-width="5"/>
    </svg>

    <div class="identity">
      <h1 class="identity-name">LENA VOSSBERG</h1>
      <p class="identity-role">Director</p>
    </div>

    <div class="contacts">
      <div class="contact">
        <svg class="contact-icon" viewBox="0 0 26 26" aria-hidden="true">
          <circle cx="13" cy="13" r="11.5" fill="#111" stroke="var(--ring-yellow)" stroke-width="2"/>
          <path d="M9 8.5c1-.8 1.8-.6 2.3.4l.7 1.5c.3.7 0 1.2-.6 1.6.6 1.4 1.5 2.4 2.8 3 .4-.6 1-.9 1.6-.6l1.5.7c1 .5 1.1 1.300 .3 2.3-2.3 2.4-9.2-4.4-8.6-8.9z" fill="var(--ring-yellow)"/>
        </svg>
        <span>0341 555.2394<br>0341 555.6127</span>
      </div>
      <div class="contact">
        <svg class="contact-icon" viewBox="0 0 26 26" aria-hidden="true">
          <circle cx="13" cy="13" r="11.5" fill="#111" stroke="var(--ring-pink)" stroke-width="2"/>
          <circle cx="13" cy="13" r="6" fill="none" stroke="var(--ring-pink)" stroke-width="1.3"/>
          <path d="M7 13h12M13 7c-2.5 3-2.5 9 0 12M13 7c2.5 3 2.5 9 0 12" fill="none" stroke="var(--ring-pink)" stroke-width="1.1"/>
        </svg>
        <span>fervolia-institut.de<br>lena@fervolia-institut.de</span>
      </div>
      <div class="contact">
        <svg class="contact-icon" viewBox="0 0 26 26" aria-hidden="true">
          <circle cx="13" cy="13" r="11.5" fill="#111" stroke="var(--ring-purple)" stroke-width="2"/>
          <path d="M13 19s-4.5-4.5-4.5-7.5a4.5 4.5 0 0 1 9 0C17.5 14.5 13 19 13 19z" fill="var(--ring-purple)"/>
          <circle cx="13" cy="11.5" r="1.6" fill="#111"/>
        </svg>
        <span>Kastanienweg 14<br>04109 Leipzig</span>
      </div>
    </div>
  </section>

  <section class="card card-back">
    <div class="brand">
      <span class="brand-dot"></span>
      <span class="brand-name">Fervolia</span>
    </div>
  </section>
</main>
</body>
</html>
```